Buch-/eBook-Cover für Traumatherapeutin
Zielgruppe
Ich bin Traumatherapeutin und schreibe ein Buch zum Thema Trauma bearbeiten.
Meine Zielgruppe sucht Heilung, Genesung, Selbstliebe etc.
Aufgabenstellung
Buchcover
Bitte erstell mir ein modernes positives inspirierendes Buchcover mit dem
Titel: 'Morgenlicht NEU entdecken“
Untertitel: „Spüre den Mut der ganz in dir wohnt“
Dr. Mira Kessow
Ich hätte gerne ein modernes Buch, das entweder einen Bezug zum Thema Trauma hat oder aber einfach stylische Schriftzüge. Bin aber auch offen für andere Vorschläge.
Dunkelblau, weiß und türkis oder auch rosa mag ich ganz gerne. Wobei Dunkelblau, weiß und türkis meine Favoriten sind und mit rosa höchstens kleinere Akzente gesetzt werden sollten.
Das Buchcover soll modern sein und direkt ansprechen. Gerne eine originelle Lösung, oder etwas Besonderes, etwas das Tiefe ausdrückt, oder man mehrmals hinsehen muss um etwas zu erkennen oder etwas das mehr Interpretationsspielraum lässt.
Gerne auch viel weiß, zumindest heller und nicht zu dunkel. Stylish, aber nicht überfrachtet.
Schreib mich gerne an, wenn du Fragen hast.
Ich habe mal zwei Beispiel von Typolösungen angehängt, die ich ganz cool fände.
Ich freue mich auf deine Ideen :-)
Ganz liebe Grüße
Mira

```html
<!DOCTYPE html>
<html lang="de">
<head>
<meta charset="utf-8">
<title>Morgenlicht neu entdecken – Buchcover</title>
<link rel="stylesheet" href="https://fonts.googleapis.com/css2?family=Open+Sans:wght@400;800&family=Dancing+Script:wght@700&family=Cookie&display=swap">
<style>
  :root {
    --backdrop: #8d8d8d;
    --paper: #ffffff;
    --band: #3f8db5;
    --title-light: #7ab7d8;
    --title-dark: #17669a;
    --subtitle: #1a6397;
    --accent-script: #6db4c4;
    --swirl-edge: #4a90b8;
    --swirl-deep: #7fc3dc;
    --swirl-light: #e4f4f8;
  }
  html, body {
    margin: 0;
    padding: 0;
    width: 849px;
    height: 1200px;
    overflow: hidden;
    background: var(--backdrop);
  }
  .book-cover {
    display: block;
    width: 849px;
    height: 1200px;
  }
  .author-name {
    font-family: "Open Sans", sans-serif;
    font-weight: 400;
    font-size: 31px;
    fill: var(--paper);
    letter-spacing: 0.5px;
  }
  .title-block {
    font-family: "Open Sans", sans-serif;
    font-weight: 800;
    fill: var(--title-light);
  }
  .title-script {
    font-family: "Dancing Script", cursive;
    font-weight: 700;
    font-size: 160px;
    fill: var(--title-dark);
  }
  .subtitle-text {
    font-family: "Open Sans", sans-serif;
    font-weight: 400;
    font-size: 30px;
    fill: var(--subtitle);
  }
  .subtitle-script {
    font-family: "Cookie", cursive;
    font-size: 66px;
    fill: var(--accent-script);
  }
  .swirl-edge {
    fill: none;
    stroke: var(--swirl-edge);
    stroke-width: 4;
    stroke-linecap: round;
    stroke-dasharray: 0.1 7;
  }
</style>
</head>
<body>
<svg class="book-cover" viewBox="0 0 849 1200" xmlns="http://www.w3.org/2000/svg">
  <defs>
    <clipPath id="cover-area">
      <rect x="66" y="91" width="717" height="1017"/>
    </clipPath>
    <radialGradient id="swirl-top" cx="0.5" cy="0.5" r="0.5">
      <stop offset="0" stop-color="var(--swirl-light)"/>
      <stop offset="0.55" stop-color="#bfe3ee"/>
      <stop offset="1" stop-color="var(--swirl-deep)"/>
    </radialGradient>
    <linearGradient id="swirl-bottom" x1="0" y1="0" x2="1" y2="0.3">
      <stop offset="0" stop-color="var(--swirl-deep)"/>
      <stop offset="0.45" stop-color="var(--swirl-light)"/>
      <stop offset="1" stop-color="#8dd0e0"/>
    </linearGradient>
    <linearGradient id="band-fill" x1="0" y1="0" x2="1" y2="0">
      <stop offset="0" stop-color="#4f97b8"/>
      <stop offset="1" stop-color="#2a84ad"/>
    </linearGradient>
  </defs>

  <rect class="cover-paper" x="66" y="91" width="717" height="1017" fill="var(--paper)"/>

  <g class="swirls" clip-path="url(#cover-area)">
    <circle role="img" aria-label="Abstrakter türkiser Wasserwirbel" cx="792" cy="74" r="331" fill="url(#swirl-top)"/>
    <circle class="swirl-edge" cx="792" cy="74" r="331"/>
    <circle role="img" aria-label="Abstrakter türkiser Wasserwirbel" cx="68" cy="1126" r="345" fill="url(#swirl-bottom)"/>
    <circle class="swirl-edge" cx="68" cy="1126" r="345"/>
  </g>

  <rect class="author-band" x="66" y="228" width="717" height="45" fill="url(#band-fill)" opacity="0.92"/>
  <text class="author-name" x="424" y="263" text-anchor="middle">DR. MIRA KESSOW</text>

  <text class="title-block" x="426" y="463" text-anchor="middle" font-size="82">MORGENLICHT</text>
  <text class="title-script" x="426" y="604" text-anchor="middle">neu</text>
  <text class="title-block" x="426" y="713" text-anchor="middle" font-size="94">ENTDECKEN</text>

  <text class="subtitle-text" x="446" y="887" text-anchor="end">Spüre den</text>
  <text class="subtitle-script" x="454" y="887">Mut</text>
  <text class="subtitle-text" x="475" y="928" text-anchor="middle">der ganz in dir wohnt!</text>
</svg>
</body>
</html>
```